brightwell - Property Management DL Card

I am after a savvy designer to cut through junk mail! so many real estate agents use flyers to promote themselves and their business and usually sales. We are a property management firm (residential) and we want to represent landlords that have existing investment properties and need a quality agent to represent them. Can you help?
DL size, will be printed and delivered to mailboxes. For a look at our website go to www.brightwellrs.com.au. Keep it simple and clutter free.
it is to be double sided - with one side to be simple and clear - just our website, logo and telephone number on the back.
attached is our logo and our telephone number is 1300 48 92 16
the above are 2 essential elements to be included + our email address: admin@brightwellrs.com.au
also attached are our transparent price list

Target Market(s)
property investors,
people that manage properties themselves
Industry/Entity Type
Property Management
- arial
Look and feel

```html
<!DOCTYPE html>
<html lang="en">
<head>
<meta charset="utf-8">
<title>brightwell – Property Management DL Card</title>
<link href="https://fonts.googleapis.com/css2?family=Open+Sans:wght@300;400&display=swap" rel="stylesheet">
<style>
  :root {
    --page-bg: #e4e4e4;
    --card-frame: #c9c4b8;
    --card-back: #b2ab9a;
    --panel-white: #ffffff;
    --ink: #262626;
    --ink-soft: #3a3a3a;
    --bullet-grey: #9a9a9a;
    --band-dark: #111111;
    --photo-wall: #e6e3de;
    --photo-floor: #c9b8a0;
  }
  * { margin: 0; padding: 0; box-sizing: border-box; }
  html, body { width: 1200px; height: 1200px; overflow: hidden; }
  body {
    background: var(--page-bg);
    font-family: "Open Sans", Arial, sans-serif;
    position: relative;
  }
  .card { position: absolute; left: 122px; width: 1000px; height: 500px; }
  .card--front { top: 57px; background: var(--card-frame); }
  .card--back { top: 636px; background: var(--card-back); }

  .front__photo {
    position: absolute; left: 22px; top: 22px; width: 644px; height: 453px;
    background: linear-gradient(180deg, var(--photo-wall) 0%, #f1efec 45%, #ebe7e1 65%, var(--photo-floor) 100%);
  }
  .front__panel {
    position: absolute; left: 666px; top: 22px; width: 310px; height: 453px;
    background: var(--panel-white);
  }
  .front__band {
    position: absolute; left: 433px; top: 116px; width: 525px; height: 26px;
    background: linear-gradient(90deg, rgba(17,17,17,0) 0%, var(--band-dark) 18%, var(--band-dark) 78%, rgba(17,17,17,0) 100%);
    color: #fff; font-size: 18px; line-height: 26px; padding-left: 104px; letter-spacing: 0.2px;
  }
  .front__benefits {
    position: absolute; left: 696px; top: 154px; list-style: none;
    font-size: 17px; line-height: 21.5px; color: var(--ink);
  }
  .front__benefits li { position: relative; padding-left: 16px; }
  .front__benefits li::before {
    content: ""; position: absolute; left: 1px; top: 7px; width: 7px; height: 7px;
    background: var(--bullet-grey); transform: rotate(45deg);
  }
  .brand-name {
    font-weight: 300; letter-spacing: -0.5px; white-space: nowrap;
  }
  .front__brand {
    position: absolute; right: 94px; top: 386px; font-size: 38px; color: var(--ink-soft);
  }

  .back__band {
    position: absolute; left: 373px; top: 261px; width: 580px; height: 66px;
    background: linear-gradient(90deg, rgba(17,17,17,0) 0%, var(--band-dark) 22%, var(--band-dark) 72%, rgba(17,17,17,0) 100%);
    display: flex; align-items: center; justify-content: center;
  }
  .back__brand { font-size: 34px; color: #ffffff; }
  .back__contact {
    position: absolute; left: 380px; top: 337px; width: 586px; text-align: center;
    font-size: 17px; line-height: 23px; color: var(--ink);
  }
  .back__contact .sep { margin: 0 5px; }
</style>
</head>
<body>
  <section class="card card--front">
    <div class="front__photo" role="img" aria-label="Photograph of a bright, modern bedroom with a white bed, low dark cabinets and a large abstract artwork"></div>
    <div class="front__panel"></div>
    <div class="front__band">Property Management specialists</div>
    <ul class="front__benefits">
      <li>No postage and admin fees</li>
      <li>No hidden extras</li>
      <li>Excellent communication</li>
      <li>Technology focussed</li>
    </ul>
    <div class="front__brand brand-name">brightwell</div>
  </section>

  <section class="card card--back">
    <div class="back__band"><span class="back__brand brand-name">brightwell</span></div>
    <div class="back__contact">
      <p>PO Box C392, Harbourside NSW, 2049<span class="sep">|</span>admin@brightwellrs.com.au</p>
      <p>1.300.48.92.16<span class="sep">|</span>www.brightwellrs.com.au</p>
    </div>
  </section>
</body>
</html>
```